Vellisant - Quality health delivered at your door

Vellisant offers home and Community Based Services for adults who wish to continue live independently in their communities. We increase accessibility to health care, reduce health care delivery gap, reduce mortality and morbidity, reduce health while promoting healthy living in the comfort of our patients communities or homes.

We provide on site services and deliver high quality healthcare at your door. Our experienced physicians coordinate care with our certified nurse practitioners and provide chronic care management, physical therapy, rehabilitation and medications management.

Target Market(s)

Older population living in independent living facilities

Industry/Entity Type

Health Care

Contact Information for Business Card

Vellisant

Number of Pages Required

4 page

Font styles to use
Sans Serif

Colors

Designer to choose colors to be used in the design.

```html
<!DOCTYPE html>
<html lang="en">
<head>
<meta charset="utf-8">
<title>Vellisant – Quality health delivered at your door</title>
<link rel="stylesheet" href="https://fonts.googleapis.com/css2?family=Raleway:wght@400;500;600;700&family=Open+Sans:wght@400;600;700&display=swap">
<style>
:root{
  --orange:#f7941d;
  --orange-dark:#e5830d;
  --green:#3e5a17;
  --green-deep:#2f4510;
  --ink:#2b2b2b;
  --muted:#8a8a8a;
  --line:#e6e6e6;
  --white:#ffffff;
  --paper:#fafafa;
}
*{box-sizing:border-box;margin:0;padding:0}
html,body{width:1200px;height:3982px;overflow:hidden}
body{position:relative;background:var(--white);font-family:"Open Sans",Arial,sans-serif;color:var(--ink)}
.abs{position:absolute}
.heading{font-family:"Raleway",Arial,sans-serif}

/* header */
.top-rule{left:0;top:0;width:1200px;height:4px;background:linear-gradient(90deg,var(--white) 0 50%,var(--orange) 50% 80%,var(--green) 80%)}
.brand{left:98px;top:36px;width:180px;text-align:center}
.brand-dot{width:94px;height:94px;border-radius:50%;background:var(--orange);border:5px solid var(--green);margin:0 auto}
.brand-name{font-family:"Raleway",Arial,sans-serif;font-weight:700;font-size:26px;color:var(--green);margin-top:6px;letter-spacing:.5px}
.contact-item{display:flex;align-items:center;gap:12px;font-size:12.5px;line-height:18px;color:#555}
.icon-ring{width:40px;height:40px;border:2px solid var(--orange);border-radius:50%;display:flex;align-items:center;justify-content:center;flex:none}
.social{display:flex;gap:8px}
.social span{width:37px;height:37px;border-radius:50%;border:2px solid var(--c);display:block}

/* hero */
.hero{left:0;top:172px;width:1200px;height:497px;background:linear-gradient(100deg,#5f7e34 0%,#8aa757 35%,#c7d6a6 60%,#a4c7b0 78%,#6f8f4a 100%)}
.hero-title{left:132px;top:330px;font-family:"Raleway",Arial,sans-serif;font-weight:700;font-size:64px;color:var(--white);letter-spacing:3px}
.hero-sub{left:132px;top:420px;width:560px;font-size:15px;line-height:24px;color:var(--white)}
.hero-btn{left:133px;top:502px;width:138px;height:44px;border:2px solid var(--white);color:var(--white);font-size:12px;font-weight:700;display:flex;align-items:center;justify-content:center;letter-spacing:.5px}
.hero-arrow{top:424px;width:34px;height:34px;border-radius:50%;background:rgba(255,255,255,.35);display:flex;align-items:center;justify-content:center}

/* nav */
.nav{left:0;top:669px;width:1200px;height:48px;background:var(--orange)}
.nav-list{position:absolute;left:101px;top:0;height:48px;display:flex;list-style:none}
.nav-list li{height:48px;padding:0 24px;display:flex;align-items:center;color:var(--white);font-size:12px;font-weight:700;letter-spacing:.3px}
.nav-list li.active{background:var(--green)}
.nav-search{left:1058px;top:683px}

/* section titles */
.section-title{left:0;width:1200px;text-align:center;font-family:"Raleway",Arial,sans-serif;font-weight:500;font-size:34px;letter-spacing:2px;color:var(--ink)}
.intro{left:240px;top:850px;width:720px;text-align:center;font-size:14px;line-height:32px;color:#555}

/* care cards */
.care-card{top:950px;width:319px;height:417px;border:1px solid var(--line);background:var(--white);box-shadow:0 2px 6px rgba(0,0,0,.06);text-align:center}
.care-photo{height:245px}
.care-card h3{font-family:"Raleway",Arial,sans-serif;font-weight:600;font-size:19px;margin:30px 0 12px}
.care-card p{font-size:13px;line-height:20px;color:var(--muted);padding:0 40px}
.read-more{display:inline-flex;align-items:center;gap:7px;font-size:12.5px;color:#444;margin-top:16px}
.read-more svg{display:block}

/* callout band */
.band{left:0;top:1452px;width:1200px;height:406px;background:linear-gradient(90deg,#6b4a3a 0%,#b58a6f 35%,#d8b49a 55%,#a67d63 80%,#5c3f33 100%);clip-path:polygon(0 0,100% 0,100% 61%,50% 100%,0 61%)}
.band-text{left:0;top:1540px;width:1200px;text-align:center;font-family:"Raleway",Arial,sans-serif;font-weight:500;font-size:36px;line-height:56px;color:var(--white)}
.btn-solid{background:var(--orange);color:var(--white);font-size:13px;font-weight:700;display:flex;align-items:center;justify-content:center;letter-spacing:.5px}

/* services */
.service{width:300px;text-align:center}
.service-icon{width:138px;height:138px;border-radius:50%;margin:0 auto;display:flex;align-items:center;justify-content:center;border:6px solid var(--green)}
.service-icon.orange{background:var(--orange)}
.service-icon.green{background:var(--green);border-color:var(--orange)}
.service h3{font-size:15px;font-weight:700;line-height:21px;margin-top:38px;min-height:42px}
.service p{font-size:13px;line-height:21px;color:var(--muted);padding:0 24px;margin-top:6px}
.service .read-more.hl{color:var(--orange)}

/* news */
.news{left:0;top:2867px;width:1200px;height:704px;background:linear-gradient(180deg,#3d4a55 0%,#6f7c86 45%,#b8b3ad 100%);clip-path:polygon(0 4%,100% 0,100% 83%,50% 100%,0 83%)}
.news-title{color:var(--white)}
.news-card{top:3027px;width:319px;height:305px;background:var(--white);border-top:5px solid var(--orange);text-align:center;padding-top:30px}
.news-month{font-family:"Raleway",Arial,sans-serif;font-size:23px;font-weight:500}
.news-year{font-family:"Raleway",Arial,sans-serif;font-size:46px;font-weight:700;line-height:54px}
.news-card p{font-size:13px;line-height:23px;color:var(--muted);padding:0 26px;margin-top:14px}

/* footer */
.foot-title{font-size:15px;font-weight:700;letter-spacing:.3px;color:var(--ink)}
.foot-text{font-size:12.5px;color:#666}
.field{width:260px;height:38px;border:1px solid var(--line);font-size:12px;color:#aaa;display:flex;align-items:center;padding-left:14px}
.foot-rule{left:98px;top:3895px;width:1004px;height:1px;background:var(--line)}
.copyright{left:0;top:3927px;width:1200px;text-align:center;font-size:12px;color:#888}
</style>
</head>
<body>

<!-- header -->
<div class="abs top-rule"></div>
<div class="abs brand"><div class="brand-dot"></div><div class="brand-name">VELLISANT</div></div>

<div class="abs contact-item" style="left:394px;top:80px">
  <span class="icon-ring"><svg width="14" height="18" viewBox="0 0 14 18"><path d="M7 1a6 6 0 0 0-6 6c0 4.5 6 10 6 10s6-5.5 6-10a6 6 0 0 0-6-6z" fill="none" stroke="#f7941d" stroke-width="1.8"/><circle cx="7" cy="7" r="2" fill="#f7941d"/></svg></span>
  <span>14 Alder Row, Maple Court<br>suite 2</span>
</div>
<div class="abs contact-item" style="left:676px;top:80px">
  <span class="icon-ring"><svg width="16" height="16" viewBox="0 0 16 16"><path d="M3 1.5l3 3-1.6 2a9 9 0 0 0 5 5l2-1.6 3 3-2 2C6 14 2 10 1.5 3.5z" fill="#f7941d"/></svg></span>
  <span>(555) - 204 - 7781<br>hello@vellisant-care.com</span>
</div>
<div class="abs social" style="left:930px;top:82px">
  <span style="--c:#3b5998"></span><span style="--c:#2aa9e0"></span><span style="--c:#3f729b"></span><span style="--c:#cc2127"></span>
</div>

<!-- hero -->
<div class="abs hero" role="img" aria-label="Smiling nurse with her arms around an elderly woman in a green garden"></div>
<div class="abs hero-title">VELLISANT</div>
<p class="abs hero-sub">Vellisant offers home and Community Based Services for adults who wish to continue live independently in their communities.</p>
<div class="abs hero-btn">READ MORE</div>
<div class="abs hero-arrow" style="left:40px"><svg width="10" height="12" viewBox="0 0 10 12"><path d="M7 1L2 6l5 5" fill="none" stroke="#fff" stroke-width="2"/></svg></div>
<div class="abs hero-arrow" style="left:1126px"><svg width="10" height="12" viewBox="0 0 10 12"><path d="M3 1l5 5-5 5" fill="none" stroke="#fff" stroke-width="2"/></svg></div>

<!-- nav -->
<nav class="abs nav">
  <ul class="nav-list">
    <li class="active">HOME</li>
    <li>ASSISTED LIVING</li>
    <li>SKILLED NURSING</li>
    <li>INDEPENDENT LIVING</li>
    <li>HOME&amp;COMMUNITY BASED SERVICES</li>
    <li>MORE</li>
  </ul>
</nav>
<svg class="abs nav-search" width="18" height="18" viewBox="0 0 18 18"><circle cx="7.5" cy="7.5" r="5.5" fill="none" stroke="#fff" stroke-width="2.2"/><path d="M11.5 11.5l5 5" stroke="#fff" stroke-width="2.4"/></svg>

<!-- welcome -->
<h2 class="abs section-title" style="top:788px">WELCOME TO VELLISANT</h2>
<p class="abs intro">Vellisant offers home and Community Based Services for adults who wish to continue to live independently in the comfort of their communities.We provide on site services and deliver high quality healthcare at your door.</p>

<div class="abs care-card" style="left:98px">
  <div class="care-photo" role="img" aria-label="Elderly man smiling with a caregiver outdoors" style="background:linear-gradient(135deg,#5b8fb9,#9cc3dc 55%,#3e6a8a)"></div>
  <h3>Personal Care</h3>
  <p>Gentle daily help with bathing, dressing and meals at home.</p>
  <span class="read-more">Read More <svg width="13" height="13" viewBox="0 0 13 13"><circle cx="6.5" cy="6.5" r="6.5" fill="#333"/><path d="M5 3.5l3 3-3 3" fill="none" stroke="#fff" stroke-width="1.6"/></svg></span>
</div>
<div class="abs care-card" style="left:438px">
  <div class="care-photo" role="img" aria-label="Nurse visiting a senior man seated in a bright room" style="background:linear-gradient(135deg,#e9e4df,#c9bfb5 55%,#f3efea)"></div>
  <h3>Monitoring visits</h3>
  <p>Regular nurse check-ins to track vitals and daily wellbeing.</p>
  <span class="read-more">Read More <svg width="13" height="13" viewBox="0 0 13 13"><circle cx="6.5" cy="6.5" r="6.5" fill="#333"/><path d="M5 3.5l3 3-3 3" fill="none" stroke="#fff" stroke-width="1.6"/></svg></span>
</div>
<div class="abs care-card" style="left:780px">
  <div class="care-photo" role="img" aria-label="Caregiver's hands resting on an elderly hand holding a cane" style="background:linear-gradient(135deg,#7fc2b3,#b9ddd2 55%,#8a6a52)"></div>
  <h3>Dementia care</h3>
  <p>Patient, familiar routines that support memory and calm days.</p>
  <span class="read-more">Read More <svg width="13" height="13" viewBox="0 0 13 13"><circle cx="6.5" cy="6.5" r="6.5" fill="#333"/><path d="M5 3.5l3 3-3 3" fill="none" stroke="#fff" stroke-width="1.6"/></svg></span>
</div>

<!-- callout band -->
<div class="abs band" role="img" aria-label="Close-up of a younger hand holding an elderly hand"></div>
<p class="abs band-text">We provide on site services and deliver high<br>quality healthcare at your door</p>
<div class="abs btn-solid" style="left:482px;top:1691px;width:236px;height:53px">CONTACT US NOW !</div>

<!-- services -->
<h2 class="abs section-title" style="top:1935px">OUR SERVICES</h2>

<div class="abs service" style="left:113px;top:2023px">
  <div class="service-icon orange"><svg width="60" height="60" viewBox="0 0 60 60" fill="none" stroke="#fff" stroke-width="4" stroke-linecap="round"><path d="M14 8v16a10 10 0 0 0 20 0V8"/><path d="M24 34v6a10 10 0 0 0 20 0v-8"/><circle cx="44" cy="27" r="5"/></svg></div>
  <h3>Comprehensive primary<br>care services</h3>
  <p>Physician visits that coordinate chronic care in your home.</p>
  <span class="read-more">Read More <svg width="13" height="13" viewBox="0 0 13 13"><circle cx="6.5" cy="6.5" r="6.5" fill="#333"/><path d="M5 3.5l3 3-3 3" fill="none" stroke="#fff" stroke-width="1.6"/></svg></span>
</div>
<div class="abs service" style="left:447px;top:2023px">
  <div class="service-icon green"><svg width="60" height="60" viewBox="0 0 60 60" fill="#fff"><circle cx="22" cy="16" r="6"/><path d="M8 46l12-20 10 8 12-6 6 4-18 10-10-6-6 10z"/><rect x="6" y="48" width="48" height="4"/></svg></div>
  <h3>Social services<br>assessment</h3>
  <p>Guidance to community benefits, housing and family support.</p>
  <span class="read-more hl">Read More <svg width="13" height="13" viewBox="0 0 13 13"><circle cx="6.5" cy="6.5" r="6.5" fill="#f7941d"/><path d="M5 3.5l3 3-3 3" fill="none" stroke="#fff" stroke-width="1.6"/></svg></span>
</div>
<div class="abs service" style="left:779px;top:2023px">
  <div class="service-icon orange"><svg width="56" height="52" viewBox="0 0 56 52" fill="#fff"><path d="M28 4L4 26h7v22h13V34h8v14h13V26h7z"/></svg></div>
  <h3>Home health assistance</h3>
  <p>Skilled nursing and wound care from certified practitioners.</p>
  <span class="read-more">Read More <svg width="13" height="13" viewBox="0 0 13 13"><circle cx="6.5" cy="6.5" r="6.5" fill="#333"/><path d="M5 3.5l3 3-3 3" fill="none" stroke="#fff" stroke-width="1.6"/></svg></span>
</div>

<div class="abs service" style="left:113px;top:2371px">
  <div class="service-icon orange"><svg width="60" height="60" viewBox="0 0 60 60" fill="#fff"><circle cx="30" cy="12" r="6"/><rect x="10" y="28" width="40" height="7" rx="3"/><rect x="8" y="40" width="44" height="4"/><rect x="12" y="44" width="4" height="10"/><rect x="44" y="44" width="4" height="10"/><path d="M22 22h16v4H22z"/></svg></div>
  <h3>Physical therapy</h3>
  <p>Rehabilitation sessions that rebuild strength and mobility safely.</p>
  <span class="read-more">Read More <svg width="13" height="13" viewBox="0 0 13 13"><circle cx="6.5" cy="6.5" r="6.5" fill="#333"/><path d="M5 3.5l3 3-3 3" fill="none" stroke="#fff" stroke-width="1.6"/></svg></span>
</div>
<div class="abs service" style="left:447px;top:2371px">
  <div class="service-icon green"><svg width="56" height="60" viewBox="0 0 56 60" fill="none" stroke="#fff" stroke-width="4" stroke-linejoin="round"><path d="M14 54V42C6 36 6 24 10 16 16 4 38 2 46 14c4 6 4 12 2 16l4 8h-6v8h-10v8"/><circle cx="28" cy="24" r="8"/></svg></div>
  <h3>Mental health</h3>
  <p>Counselling that eases loneliness, stress and low mood.</p>
  <span class="read-more hl">Read More <svg width="13" height="13" viewBox="0 0 13 13"><circle cx="6.5" cy="6.5" r="6.5" fill="#f7941d"/><path d="M5 3.5l3 3-3 3" fill="none" stroke="#fff" stroke-width="1.6"/></svg></span>
</div>
<div class="abs service" style="left:779px;top:2371px">
  <div class="service-icon orange"><svg width="48" height="58" viewBox="0 0 48 58" fill="#fff"><path d="M12 2C4 2 2 10 3 18c1 8 5 12 6 22 1 8 2 16 6 16 5 0 4-16 9-16s4 16 9 16c4 0 5-8 6-16 1-10 5-14 6-22 1-8-1-16-9-16-6 0-8 4-12 4S18 2 12 2z"/></svg></div>
  <h3>Dental health</h3>
  <p>Routine checks and cleaning to keep smiles healthy.</p>
  <span class="read-more">Read More <svg width="13" height="13" viewBox="0 0 13 13"><circle cx="6.5" cy="6.5" r="6.5" fill="#333"/><path d="M5 3.5l3 3-3 3" fill="none" stroke="#fff" stroke-width="1.6"/></svg></span>
</div>

<div class="abs btn-solid" style="left:482px;top:2735px;width:236px;height:50px">VIEW ALL SERVICES</div>

<!-- news -->
<div class="abs news" role="img" aria-label="Nurse with a stethoscope caring for a patient in a hospital bed, with a small silhouette of an elderly couple"></div>
<h2 class="abs section-title news-title" style="top:2933px">OUR LATEST NEWS</h2>

<div class="abs news-card" style="left:100px">
  <div class="news-month">MARCH</div><div class="news-year">2017</div>
  <p>Our nurses began weekly wellness visits across three new communities.</p>
  <span class="read-more">Read More <svg width="13" height="13" viewBox="0 0 13 13"><circle cx="6.5" cy="6.5" r="6.5" fill="#333"/><path d="M5 3.5l3 3-3 3" fill="none" stroke="#fff" stroke-width="1.6"/></svg></span>
</div>
<div class="abs news-card" style="left:440px">
  <div class="news-month">JUNE</div><div class="news-year">2017</div>
  <p>A new falls prevention program helps residents stay steady at home.</p>
  <span class="read-more">Read More <svg width="13" height="13" viewBox="0 0 13 13"><circle cx="6.5" cy="6.5" r="6.5" fill="#333"/><path d="M5 3.5l3 3-3 3" fill="none" stroke="#fff" stroke-width="1.6"/></svg></span>
</div>
<div class="abs news-card" style="left:780px">
  <div class="news-month">JULY</div><div class="news-year">2017</div>
  <p>Medication reviews now come with every home health visit.</p>
  <span class="read-more">Read More <svg width="13" height="13" viewBox="0 0 13 13"><circle cx="6.5" cy="6.5" r="6.5" fill="#333"/><path d="M5 3.5l3 3-3 3" fill="none" stroke="#fff" stroke-width="1.6"/></svg></span>
</div>

<!-- footer -->
<div class="abs brand" style="top:3650px"><div class="brand-dot"></div><div class="brand-name">VELLISANT</div></div>

<div class="abs" style="left:329px;top:3652px">
  <div class="foot-title">SUBSCRIBE TO NEWSLETTER</div>
  <div class="foot-text" style="margin-top:22px;font-size:11.5px">Monthly health tips for you and your family.</div>
  <div class="field" style="margin-top:14px">Enter Mail.....</div>
  <div class="btn-solid" style="margin-top:14px;width:111px;height:38px;font-size:11px">SUBSCRIBE</div>
</div>

<div class="abs" style="left:640px;top:3652px">
  <div class="foot-title">CONTACT US</div>
  <div class="contact-item" style="margin-top:22px;gap:16px">
    <svg width="14" height="18" viewBox="0 0 14 18"><path d="M7 1a6 6 0 0 0-6 6c0 4.5 6 10 6 10s6-5.5 6-10a6 6 0 0 0-6-6z" fill="none" stroke="#888" stroke-width="1.6"/><circle cx="7" cy="7" r="2" fill="#888"/></svg>
    <span>14 Alder Row, Maple Court<br>suite 2</span>
  </div>
  <div class="contact-item" style="margin-top:18px;gap:16px">
    <svg width="14" height="14" viewBox="0 0 16 16"><path d="M3 1.5l3 3-1.6 2a9 9 0 0 0 5 5l2-1.6 3 3-2 2C6 14 2 10 1.5 3.5z" fill="#888"/></svg>
    <span>(555) - 204 - 7781</span>
  </div>
  <div class="contact-item" style="margin-top:18px;gap:16px">
    <svg width="16" height="12" viewBox="0 0 16 12"><rect x="1" y="1" width="14" height="10" fill="none" stroke="#888" stroke-width="1.4"/><path d="M1 1l7 6 7-6" fill="none" stroke="#888" stroke-width="1.4"/></svg>
    <span>hello@vellisant-care.com</span>
  </div>
</div>

<div class="abs" style="left:927px;top:3652px">
  <div class="foot-title">FOLLOW US</div>
  <div class="social" style="margin-top:28px">
    <span style="--c:#3b5998"></span><span style="--c:#2aa9e0"></span><span style="--c:#3f729b"></span><span style="--c:#cc2127"></span>
  </div>
</div>

<div class="abs foot-rule"></div>
<p class="abs copyright">© copyright 2017 Vellisant. All Rights Reserved</p>

</body>
</html>
```